Marwick Law Letterhead

We need a new letterhead design for a Law Firm. The address for the law firm is 1475 Calloway Street, Suite 210, Houston, Texas 77041. Phone Number: 832-361-9027; Fax Number: 832-614-7359. The logo is uploaded to the project.

```html
<!DOCTYPE html>
<html lang="en">
<head>
<meta charset="utf-8">
<title>Marwick Law Letterhead</title>
<link rel="stylesheet" href="https://fonts.googleapis.com/css2?family=Montserrat:wght@400;500;600&display=swap">
<style>
  :root {
    --navy: #172d5c;
    --red: #d71a28;
    --red-dark: #6e0712;
    --ink: #1c1c1c;
    --paper: #ffffff;
    --backdrop: #e6e6e8;
  }
  * { box-sizing: border-box; margin: 0; padding: 0; }
  html, body {
    width: 1200px; height: 960px; overflow: hidden;
    background: var(--backdrop);
    font-family: "Montserrat", sans-serif;
    color: var(--ink);
  }
  .letterhead {
    position: absolute; left: 280px; top: 26px;
    width: 640px; height: 908px;
    background: var(--paper);
    box-shadow: 0 4px 18px rgba(0,0,0,.12);
    overflow: hidden;
  }
  .band { position: absolute; left: 0; width: 640px; height: 34px; display: block; }
  .band--top { top: 0; }
  .band--bottom { bottom: 0; }

  .brand {
    position: absolute; left: 50px; top: 66px;
    display: flex; align-items: center; gap: 12px;
  }
  .brand__mark {
    width: 40px; height: 40px; border-radius: 50%;
    background: var(--navy);
  }
  .brand__name {
    font-size: 26px; font-weight: 600; color: var(--navy);
    letter-spacing: .5px; line-height: 1;
  }

  .address {
    position: absolute; left: 50px; top: 130px;
    font-size: 11px; line-height: 1.4; font-weight: 500; font-style: normal;
  }
  .recipient {
    position: absolute; left: 50px; top: 196px;
    font-size: 11px; line-height: 1.45;
  }
  .body {
    position: absolute; left: 50px; top: 276px; width: 540px;
    font-size: 11px; line-height: 1.45;
  }
  .body p { margin-bottom: 14px; }
  .body p:last-child { margin-bottom: 0; }

  .signoff {
    position: absolute; left: 50px; top: 750px;
    font-size: 12px; font-weight: 500;
  }
  .signature {
    position: absolute; left: 58px; top: 772px;
    width: 100px; height: 28px; border-radius: 4px;
    background: linear-gradient(90deg, #d9d9d9, #efefef);
  }
  .contact {
    position: absolute; left: 50px; top: 814px;
    list-style: none; font-size: 11px; font-weight: 500;
  }
  .contact li { display: flex; align-items: center; gap: 8px; margin-bottom: 4px; }
  .contact svg { width: 11px; height: 11px; fill: var(--red); }
</style>
</head>
<body>
  <main class="letterhead">
    <svg class="band band--top" viewBox="0 0 640 34" aria-hidden="true">
      <defs>
        <linearGradient id="redTop" x1="0" x2="1">
          <stop offset="0" stop-color="#d71a28"/>
          <stop offset=".6" stop-color="#d71a28"/>
          <stop offset="1" stop-color="#6e0712"/>
        </linearGradient>
      </defs>
      <polygon points="0,0 392,0 380,34 0,34" fill="#172d5c"/>
      <polygon points="402,0 640,0 640,22 394,22" fill="url(#redTop)"/>
    </svg>

    <header class="brand">
      <span class="brand__mark"></span>
      <span class="brand__name">Marwick Law</span>
    </header>

    <address class="address">
      1475 Calloway Street,<br>Suite 210, Houston,<br>Texas 77041
    </address>

    <div class="recipient">
      Mr/s<br>First Name and Last Name<br>Company Name<br>Address
    </div>

    <section class="body">
      <p>Lorem ipsum dolor sit amet,consectetur adipiscing sed do eiusmod tempor incididunt laboreet dolore magna aliqua.Ut enim ad minim veniam, quis nostrud exercitation ullamco laboris nisi ut aliquip exea commodo consequat.Lorem ipsum dolor sit amet,consectetur adipiscing sed do eiusmod tempor incididunt labore et dolore magna aliqua. Ut enim</p>
      <p>Lorem ipsum dolor sit amet, consectetur adipiscing sed do eiusmod tempor incididunt labore et dolore magna aliqua. Ut enim ad minim veniam, quis nostrud exercitation ullamco laboris nisi ut aliquip exea commodo consequat.Duis aute irure dolor in reprehenderit in voluptate velit esse cillum irure dolor in reprehenderit in voluptate velit esse irure</p>
      <p>Lorem ipsum dolor sit amet, consectetur adipiscing sed do eiusmod tempor incididunt labore et dolore magna aliqua. consequat. Duis aute irure dolor in.reprehenderit in voluptate velit esse cillum dolore eu fugiat nulla pariatur. Excepteur sint occaecat cupidatat non proident, sunt in culpa qui officia deserunt mollit,</p>
      <p>Lorem ipsum dolor sit amet, consectetur adipiscing sed do eiusmod tempor incididunt labore et dolore magna aliqua. Ut enim Lorem ipsum dolor sit amet, consectetur adipiscing sed do eiusmod tempor incididunt labore et dolore magna aliqua. Ut enim Lorem ipsum aliqua.ipsum</p>
      <p>Lorem ipsum dolor sit amet, consectetur adipiscing sed do eiusmod tempor incididunt labore et dolore magna aliqua. Ut enim ad minim veniam, quis nostrud exercitation ullamco laboris nisi ut aliquip exea commodo consequat.Duis aute irure dolor in reprehenderit in voluptate velit esse cillum irure dolor in reprehenderit in voluptate velit esse irure</p>
      <p>Lorem ipsum dolor sit amet, consectetur adipiscing sed do eiusmod tempor incididunt labore et dolore magna aliqua. Ut enim ad minim veniam, quis nostrud exercitation ullamco laboris nisi ut aliquip exea commodo consequat.Duis aute irure dolor in reprehenderit in voluptate velit esse cillum irure dolor in reprehenderit in voluptate velit esse irure</p>
    </section>

    <p class="signoff">Regards</p>
    <div class="signature" role="img" aria-label="Handwritten signature of the sender"></div>

    <ul class="contact">
      <li>
        <svg viewBox="0 0 24 24" aria-hidden="true"><path d="M6.6 10.8a15.1 15.1 0 0 0 6.6 6.6l2.2-2.2a1 1 0 0 1 1-.25 11.4 11.4 0 0 0 3.6.57 1 1 0 0 1 1 1V20a1 1 0 0 1-1 1A17 17 0 0 1 3 4a1 1 0 0 1 1-1h3.5a1 1 0 0 1 1 1c0 1.25.2 2.45.57 3.57a1 1 0 0 1-.25 1z"/></svg>
        832-361-9027
      </li>
      <li>
        <svg viewBox="0 0 24 24" aria-hidden="true"><path d="M6 2h10l2 2v5H6zM4 10h16a2 2 0 0 1 2 2v6h-4v4H6v-4H2v-6a2 2 0 0 1 2-2zm4 7v3h8v-3z"/></svg>
        832-614-7359
      </li>
    </ul>

    <svg class="band band--bottom" viewBox="0 0 640 34" aria-hidden="true">
      <defs>
        <linearGradient id="redBottom" x1="0" x2="1">
          <stop offset="0" stop-color="#d71a28"/>
          <stop offset=".6" stop-color="#d71a28"/>
          <stop offset="1" stop-color="#6e0712"/>
        </linearGradient>
      </defs>
      <polygon points="0,0 420,0 408,34 0,34" fill="#172d5c"/>
      <polygon points="432,-14 640,-14 640,34 420,34" fill="url(#redBottom)"/>
    </svg>
  </main>
</body>
</html>
```